Briloran Clear Springs needs a new business card design (we produce and sell pure bottled water)

We need a clean modern design for our new business cards, We have an existing logo which ultimately cannot be changed, however it could be slighty improved and the colours adjusted. We have this existing logo on all of our bottles, vehicles etc.

Our company slogan is "Pure down to the last drop".
Along with our relevant company information
(Address, phone, website email etc) we will only be using names and not putting position titles for flexibilty.

We are looking for a clean, minimalist modern design.

You can view our website (if need of an update also!) to see our business.

Industry/Entity Type

Business

Contact Information for Business Card

Staff Name : XXXXXX XXXXXX
Address : 9/41 Tavenor St
Halden Rise QLD 4172
Staff Mobile Number : 04XX XXX XXX
Office Phone Number : 07 3918 2457
Staff Email Address : XXXX@brilorancleargo.com.au
Website : www.brilorancleargo.com.au

Font styles to use
Sans Serif

Colors
cee9f5
33a6d7
0492cd
0455a3
3276b5
85abd2
cedeed

Requirements
Must have
• The ability to edit and change the staff members details as we will need to edit for each respective staff member (7 in total)

```html
<!DOCTYPE html>
<html lang="en">
<head>
<meta charset="utf-8">
<title>Briloran Clear Springs — Business Card</title>
<link href="https://fonts.googleapis.com/css2?family=Abril+Fatface&family=Barlow+Condensed:wght@400;600;700&display=swap" rel="stylesheet">
<style>
  :root {
    --backdrop: #5ebccd;
    --navy: #0e3f7c;
    --deep-blue: #0455a3;
    --wave-tint: #e6eef6;
    --wave-line: #cedeed;
    --drop-tint: #c9d9ea;
    --white: #ffffff;
    --edge: #bfe8e2;
  }
  * { box-sizing: border-box; margin: 0; padding: 0; }
  html, body { width: 1200px; height: 818px; overflow: hidden; }
  body {
    background: var(--backdrop);
    font-family: "Barlow Condensed", sans-serif;
    position: relative;
  }
  .card {
    position: absolute;
    top: 250px;
    width: 520px;
    height: 318px;
    border-radius: 6px;
    overflow: hidden;
    box-shadow: 0 0 0 3px var(--edge), 0 14px 30px rgba(0, 40, 70, 0.25);
  }
  .card--front { left: 50px; }
  .card--back { left: 630px; }

  .wave-field {
    position: absolute;
    inset: 0;
    background: linear-gradient(180deg, var(--wave-tint), var(--wave-line));
  }

  /* Front */
  .slogan {
    position: absolute;
    left: 40px;
    top: 36px;
    font-family: "Abril Fatface", serif;
    font-size: 66px;
    line-height: 0.92;
    color: var(--navy);
    letter-spacing: -0.5px;
  }
  .drop-art {
    position: absolute;
    right: 40px;
    bottom: 50px;
    width: 70px;
    height: 90px;
    border-radius: 50% 50% 50% 50% / 60% 60% 40% 40%;
    background: radial-gradient(circle at 40% 60%, var(--white), var(--drop-tint));
  }

  /* Back */
  .brand {
    position: absolute;
    left: 30px;
    top: 40px;
    display: flex;
    align-items: center;
    gap: 10px;
  }
  .brand__mark {
    width: 20px;
    height: 20px;
    border-radius: 50%;
    background: var(--deep-blue);
  }
  .brand__name {
    font-weight: 700;
    font-size: 20px;
    letter-spacing: 1px;
    text-transform: uppercase;
    color: var(--deep-blue);
    max-width: 130px;
    line-height: 1.05;
  }
  .staff {
    position: absolute;
    left: 200px;
    top: 34px;
  }
  .staff__name {
    font-family: "Abril Fatface", serif;
    font-size: 40px;
    color: var(--navy);
    line-height: 1;
    margin-bottom: 14px;
  }
  .contact-line {
    display: flex;
    align-items: center;
    gap: 8px;
    font-size: 19px;
    color: var(--navy);
    text-transform: uppercase;
    letter-spacing: 0.5px;
    margin-bottom: 6px;
  }
  .contact-line svg { width: 20px; height: 20px; flex: none; }
  .office-band {
    position: absolute;
    left: 0;
    right: 0;
    bottom: 0;
    height: 98px;
    background: var(--navy);
    padding: 14px 0 0 200px;
    color: var(--white);
    font-size: 19px;
    line-height: 1.4;
    text-transform: uppercase;
    letter-spacing: 0.6px;
  }
</style>
</head>
<body>

  <section class="card card--front" aria-label="Business card front">
    <div class="wave-field" role="img" aria-label="Blue wavy line pattern"></div>
    <h1 class="slogan">Pure down<br>to the last<br>drop</h1>
    <div class="drop-art" role="img" aria-label="Water drop illustration"></div>
  </section>

  <section class="card card--back" aria-label="Business card back">
    <div class="wave-field" role="img" aria-label="Grey wavy line pattern"></div>

    <div class="brand">
      <span class="brand__mark"></span>
      <span class="brand__name">Briloran Clear Springs</span>
    </div>

    <div class="staff">
      <p class="staff__name">Staff Name</p>
      <p class="contact-line">
        <svg viewBox="0 0 20 20" aria-hidden="true"><circle cx="10" cy="10" r="10" fill="#0e3f7c"/><rect x="5" y="6.5" width="10" height="7" rx="1" fill="none" stroke="#fff" stroke-width="1.3"/><path d="M5 7l5 4 5-4" fill="none" stroke="#fff" stroke-width="1.3"/></svg>
        XXXX@brilorancleargo.com.au
      </p>
      <p class="contact-line">
        <svg viewBox="0 0 20 20" aria-hidden="true"><circle cx="10" cy="10" r="10" fill="#0e3f7c"/><rect x="7" y="4.5" width="6" height="11" rx="1.2" fill="none" stroke="#fff" stroke-width="1.3"/><circle cx="10" cy="13.4" r="0.7" fill="#fff"/></svg>
        04XX XXX XXX
      </p>
    </div>

    <div class="office-band">
      <p>9/41 Tavenor St, Halden Rise QLD 4172</p>
      <p>07 3918 2457</p>
      <p>www.brilorancleargo.com.au</p>
    </div>
  </section>

</body>
</html>
```